Wheels for Heroes Website Design

We need a NEW design and uploaded to Hostrova.com. Here is the current site: http://www.wheelsforheroes.org

Need a form like this:

https://youthautogifts.org/

Coding

Coded - Design and coding required

Number of Pages Required

1 page

```html
<!DOCTYPE html>
<html lang="en">
<head>
<meta charset="utf-8">
<title>Rides For Youth – Donate Your Car</title>
<link href="https://fonts.googleapis.com/css2?family=Bebas+Neue&family=Montserrat:wght@400;500;600;700&display=swap" rel="stylesheet">
<style>
:root{
  --red:#ed1c24;
  --red-dark:#d3141b;
  --ink:#222222;
  --text:#444444;
  --muted:#666666;
  --soft:#f4f4f4;
  --section:#f7f7f7;
  --pink:#fde6e7;
  --footer:#2a2a2a;
  --white:#ffffff;
}
*{box-sizing:border-box;margin:0;padding:0}
html,body{width:1200px;height:3277px;overflow:hidden}
body{position:relative;font-family:"Montserrat",sans-serif;color:var(--text);background:var(--white)}
.display{font-family:"Bebas Neue",sans-serif;font-weight:400;letter-spacing:.5px}
.abs{position:absolute}

/* header */
.site-header{position:absolute;left:0;top:0;width:1200px;height:112px;background:var(--white)}
.brand{position:absolute;left:172px;top:36px;display:flex;align-items:center;gap:10px}
.brand-mark{width:34px;height:34px;background:var(--red)}
.brand-name{font-family:"Bebas Neue",sans-serif;font-size:32px;color:var(--red);line-height:1}
.main-nav{position:absolute;left:416px;top:47px;display:flex;gap:20px;font-size:12.5px;color:var(--ink);font-weight:500}
.call-box{position:absolute;left:760px;top:0;width:440px;height:112px;background:var(--red);color:var(--white)}
.call-box svg{position:absolute;left:22px;top:18px}
.call-label{position:absolute;left:62px;top:14px;font-size:24px;letter-spacing:2px}
.call-number{position:absolute;left:64px;top:34px;font-size:42px;letter-spacing:1px}
.call-hours{position:absolute;left:67px;top:83px;font-size:10px;font-weight:600}

/* hero */
.hero{position:absolute;left:0;top:112px;width:1200px;height:510px;
  background:linear-gradient(100deg,#6f7a6c 0%,#9aa59a 30%,#b9c3ce 60%,#a8b4a4 85%,#7f8a70 100%)}
.hero-title{position:absolute;right:172px;top:92px;font-size:62px;color:var(--white);text-shadow:0 2px 4px rgba(0,0,0,.35)}
.hero-sub{position:absolute;right:172px;top:182px;width:500px;text-align:right;font-size:18.5px;line-height:26px;color:var(--white)}
.btn-red{background:var(--red);color:var(--white);display:flex;align-items:center;justify-content:center}
.hero-btn{position:absolute;left:907px;top:270px;width:120px;height:57px;font-size:22px}
.hero-arrow{position:absolute;top:200px}

/* steps */
.steps-intro{position:absolute;top:698px;width:1200px;text-align:center;font-size:18px;color:var(--ink)}
.steps-title{position:absolute;top:736px;width:1200px;text-align:center;font-size:46px;color:var(--red)}
.step{position:absolute;top:850px;width:244px;height:244px;border-radius:50%;background:var(--soft);text-align:center}
.step.active{background:var(--pink)}
.step svg{position:absolute;left:92px;top:32px}
.step h3{position:absolute;top:110px;width:100%;font-size:29px;color:var(--ink)}
.step.active h3{color:var(--red)}
.step p{position:absolute;top:152px;left:20px;right:20px;font-size:13.5px;line-height:20px;color:var(--text)}
.step-num{position:absolute;width:80px;height:80px;border-radius:50%;background:#333;color:var(--white);font-size:42px;display:flex;align-items:center;justify-content:center;top:847px}
.step-num.active{background:var(--red)}

/* why */
.why{position:absolute;left:0;top:1183px;width:1200px;height:543px;background:var(--section)}
.why-title{position:absolute;left:172px;top:137px;font-size:45px;color:var(--red)}
.why-list{position:absolute;left:172px;top:206px;list-style:none}
.why-list li{display:flex;align-items:center;gap:11px;height:30px;font-size:13px;color:var(--text)}
.donate-form{position:absolute;left:719px;top:73px;width:310px;height:397px;background:#f2f2f2;border:2px solid #d6d6d6;border-top:none}
.form-head{position:absolute;left:-2px;top:0;width:310px;height:78px;color:var(--white);text-align:center}
.form-head svg{position:absolute;left:0;top:0}
.form-head h3{position:relative;font-size:26px;padding-top:14px}
.form-head p{position:relative;font-size:12.5px;font-weight:600;margin-top:1px}
.field{position:absolute;height:35px;background:var(--white);border:1px solid #cfcfcf;font-size:11px;color:#555;padding-left:8px;display:flex;align-items:center}
.field.select::after{content:"";position:absolute;right:10px;top:15px;border:4px solid transparent;border-top:5px solid #333}
.form-btn{position:absolute;left:15px;top:337px;width:105px;height:35px;font-size:12.5px;font-weight:600}

/* benefits */
.flag-band{position:absolute;left:0;top:1832px;width:1200px;height:423px;
  background:linear-gradient(170deg,#ffffff 0%,#ffffff 18%,#2d3e7a 35%,#b8bccc 55%,#c42a33 75%,#9e1a22 100%)}
.benefit{position:absolute;top:1862px;width:163px;height:138px;background:var(--white);border:3px solid var(--red);text-align:center;font-size:14px;line-height:18px;color:var(--red)}
.benefit.dark{border-color:#333;color:#333}
.benefit svg{position:absolute;left:56px;top:20px}
.benefit span{position:absolute;left:6px;right:6px;bottom:16px}

/* faq */
.faq-photo{position:absolute;left:705px;top:2320px;width:495px;height:562px;
  background:linear-gradient(160deg,#6e6a52 0%,#8a8a6c 35%,#d9d2c2 55%,#5c5a44 100%)}
.faq-title{position:absolute;left:172px;top:2375px;font-size:45px;color:var(--red)}
.faq-item{position:absolute;left:172px;width:428px;height:38px;border:2px solid #d4d4d4;background:#f1f1f1;border-radius:5px;font-size:14px;color:var(--ink);display:flex;align-items:center;padding-left:50px}
.faq-item .toggle{position:absolute;left:3px;top:3px;width:30px;height:28px;border-radius:4px;background:#333;color:var(--white);display:flex;align-items:center;justify-content:center;font-size:22px;font-weight:600}
.faq-item .chev{position:absolute;right:12px;top:12px}
.faq-item.open{background:var(--red);border-color:var(--red);color:var(--white)}
.faq-item.open .toggle{background:var(--white);color:var(--red)}
.faq-answer{position:absolute;left:172px;top:2518px;width:470px;font-size:13.5px;line-height:22px;color:var(--text)}

/* footer */
.site-footer{position:absolute;left:0;top:2882px;width:1200px;height:395px;background:var(--footer);border-top:5px solid var(--red);color:var(--white)}
.foot-call svg{position:absolute;left:172px;top:137px}
.foot-label{position:absolute;left:214px;top:133px;font-size:25px;letter-spacing:2px}
.foot-number{position:absolute;left:216px;top:154px;font-size:42px}
.foot-hours{position:absolute;left:218px;top:200px;font-size:10.5px;font-weight:600}
.foot-head{position:absolute;top:97px;font-size:25px}
.foot-head::after{content:"";position:absolute;left:0;top:36px;width:56px;height:2px;background:var(--white)}
.foot-nav{position:absolute;left:514px;top:160px;list-style:none;font-size:12.5px}
.foot-nav li{display:flex;align-items:center;gap:10px;height:22.5px}
.foot-about{position:absolute;left:725px;top:160px;width:305px;font-size:11.5px;line-height:22.5px;text-align:justify}
.foot-rule{position:absolute;left:172px;top:305px;width:856px;height:1px;background:#bdbdbd}
.copyright{position:absolute;top:337px;width:1200px;text-align:center;font-size:13.5px}
</style>
</head>
<body>

<header class="site-header">
  <div class="brand"><span class="brand-mark"></span><span class="brand-name">RIDES FOR YOUTH</span></div>
  <nav class="main-nav"><span>HOW TO DONATE</span><span>WHY DONATE</span><span>FAQ</span><span>ABOUT</span></nav>
  <div class="call-box">
    <svg width="30" height="48" viewBox="0 0 30 48"><rect x="2" y="2" width="26" height="44" rx="5" fill="none" stroke="#fff" stroke-width="3.5"/><line x1="2" y1="36" x2="28" y2="36" stroke="#fff" stroke-width="3"/></svg>
    <div class="call-label display">CALL TODAY TO DONATE</div>
    <div class="call-number display">1-800-555-0142</div>
    <div class="call-hours">Live Operators Available-7 Days A Week</div>
  </div>
</header>

<section class="hero" role="img" aria-label="Photo of a smiling soldier holding a young child outdoors">
  <svg class="hero-arrow" style="left:78px" width="30" height="52" viewBox="0 0 30 52"><polyline points="27,2 3,26 27,50" fill="none" stroke="#fff" stroke-width="2.5"/></svg>
  <svg class="hero-arrow" style="left:1098px" width="30" height="52" viewBox="0 0 30 52"><polyline points="3,2 27,26 3,50" fill="none" stroke="#fff" stroke-width="2.5"/></svg>
  <h1 class="hero-title display">RIDES FOR YOUTH</h1>
  <p class="hero-sub">We provide financial support for a group of children with rare eye defects</p>
  <div class="hero-btn btn-red display">READ MORE</div>
</section>

<p class="steps-intro">There are just 3 simple steps!</p>
<h2 class="steps-title display">DONATING YOUR CAR TO KID IS AS EASY AS...</h2>

<div class="step" style="left:173px">
  <svg width="60" height="60" viewBox="0 0 60 60" fill="none" stroke="#222" stroke-width="2.5"><path d="M14 6l8 10-5 6c3 8 10 15 18 19l6-5 10 8-6 8C28 50 10 32 6 14z"/><path d="M32 8a20 20 0 0 1 20 20M32 16a12 12 0 0 1 12 12"/></svg>
  <h3 class="display">CONTACT US</h3>
  <p>Fill out the above form or call (866) 555-0178</p>
</div>
<div class="step active" style="left:478px">
  <svg width="60" height="60" viewBox="0 0 60 60" fill="none" stroke="#ed1c24" stroke-width="3"><circle cx="30" cy="32" r="24"/><path d="M30 16v16l-8-6M30 32l9-7"/><path d="M22 5h16"/></svg>
  <h3 class="display">SCHEDULE PICKUP</h3>
  <p>We'll pickup your vehicle at your convenience free of charge.</p>
</div>
<div class="step" style="left:766px">
  <svg width="60" height="60" viewBox="0 0 60 60" fill="none" stroke="#222" stroke-width="2.5"><rect x="6" y="6" width="22" height="14" rx="2"/><circle cx="18" cy="30" r="5"/><path d="M8 48c0-8 5-11 10-11s10 3 10 11z"/><circle cx="40" cy="28" r="6"/><path d="M28 50c0-9 6-13 12-13s12 4 12 13z"/></svg>
  <h3 class="display">TAX DEDUCTION</h3>
  <p>You may qualify for a top tax deduction.</p>
</div>
<div class="step-num display" style="left:356px">01</div>
<div class="step-num active display" style="left:657px">02</div>
<div class="step-num display" style="left:947px">03</div>

<section class="why">
  <h2 class="why-title display">WHY DONATE YOUR CAR TO KIDS?</h2>
  <ul class="why-list">
    <li><svg width="14" height="12" viewBox="0 0 14 12"><path d="M1 6l4 4 8-9" fill="none" stroke="#ed1c24" stroke-width="2.5"/></svg>Nemo enim ipsam voluptatem quia voluptas sit aspernatur aut odit aut fugit</li>
    <li><svg width="14" height="12" viewBox="0 0 14 12"><path d="M1 6l4 4 8-9" fill="none" stroke="#ed1c24" stroke-width="2.5"/></svg>Sed quia consequuntur magni dolores eos qui ratione voluptatem</li>
    <li><svg width="14" height="12" viewBox="0 0 14 12"><path d="M1 6l4 4 8-9" fill="none" stroke="#ed1c24" stroke-width="2.5"/></svg>Nemo enim ipsam voluptatem quia voluptas sit aspernatur aut odit aut fugit</li>
    <li><svg width="14" height="12" viewBox="0 0 14 12"><path d="M1 6l4 4 8-9" fill="none" stroke="#ed1c24" stroke-width="2.5"/></svg>Sed quia consequuntur magni dolores eos qui ratione voluptatem</li>
    <li><svg width="14" height="12" viewBox="0 0 14 12"><path d="M1 6l4 4 8-9" fill="none" stroke="#ed1c24" stroke-width="2.5"/></svg>Nemo enim ipsam voluptatem quia voluptas sit aspernatur aut odit aut fugit</li>
    <li><svg width="14" height="12" viewBox="0 0 14 12"><path d="M1 6l4 4 8-9" fill="none" stroke="#ed1c24" stroke-width="2.5"/></svg>Sed quia consequuntur magni dolores eos qui ratione voluptatem</li>
    <li><svg width="14" height="12" viewBox="0 0 14 12"><path d="M1 6l4 4 8-9" fill="none" stroke="#ed1c24" stroke-width="2.5"/></svg>Nemo enim ipsam voluptatem quia voluptas sit aspernatur aut odit aut fugit</li>
    <li><svg width="14" height="12" viewBox="0 0 14 12"><path d="M1 6l4 4 8-9" fill="none" stroke="#ed1c24" stroke-width="2.5"/></svg>Sed quia consequuntur magni dolores eos qui ratione voluptatem</li>
  </ul>

  <form class="donate-form">
    <div class="form-head">
      <svg width="310" height="78" viewBox="0 0 310 78"><polygon points="0,0 310,0 310,64 155,78 0,64" fill="#ed1c24"/></svg>
      <h3 class="display">DONATE YOUR CAR ONLINE</h3>
      <p>Full Tax Deduction - Running or Not</p>
    </div>
    <div class="field" style="left:15px;top:113px;width:131px">First Name</div>
    <div class="field" style="left:161px;top:113px;width:131px">Last Name</div>
    <div class="field" style="left:15px;top:158px;width:131px">Daytime Phone</div>
    <div class="field" style="left:161px;top:158px;width:131px">Email</div>
    <div class="field" style="left:15px;top:203px;width:277px">Zip Code</div>
    <div class="field select" style="left:15px;top:248px;width:131px">Choose Year</div>
    <div class="field select" style="left:161px;top:248px;width:131px">Choose Make</div>
    <div class="field" style="left:15px;top:293px;width:277px">Vehicle Model</div>
    <div class="form-btn btn-red">DONATE NOW</div>
  </form>
</section>

<div class="flag-band" role="img" aria-label="Photo of a waving American flag"></div>
<div class="benefit" style="left:170px">
  <svg width="52" height="52" viewBox="0 0 52 52" fill="none" stroke="#ed1c24" stroke-width="3.5"><circle cx="24" cy="28" r="21"/><path d="M14 26l9 9 24-28"/></svg>
  <span>You have no costs</span>
</div>
<div class="benefit dark" style="left:344px">
  <svg width="52" height="52" viewBox="0 0 52 52" fill="none" stroke="#333" stroke-width="3"><rect x="2" y="24" width="24" height="14"/><path d="M26 38V28h10l8 10z"/><circle cx="10" cy="42" r="4" fill="#333"/><circle cx="36" cy="42" r="4" fill="#333"/><path d="M30 22l12-18 6 16"/></svg>
  <span>Free towing, running or not</span>
</div>
<div class="benefit" style="left:518px">
  <svg width="52" height="52" viewBox="0 0 52 52" fill="none" stroke="#ed1c24" stroke-width="2.5"><rect x="10" y="4" width="32" height="44"/><path d="M16 16h20M16 24h20M16 32h20M16 40h14"/></svg>
  <span>We issue you an IRS tax receipt</span>
</div>
<div class="benefit dark" style="left:692px">
  <svg width="52" height="52" viewBox="0 0 52 52" fill="none" stroke="#333" stroke-width="2.5"><path d="M10 6h26v36H10z"/><path d="M15 14h16M15 22h16M15 30h12"/><rect x="22" y="38" width="26" height="10" rx="5" fill="#333"/></svg>
  <span>We take care of all paperwork</span>
</div>
<div class="benefit" style="left:866px">
  <svg width="52" height="52" viewBox="0 0 52 52" fill="none" stroke="#ed1c24" stroke-width="2.5"><path d="M8 4h24l8 8v34H8z"/><path d="M14 16h14M14 24h10M14 32h8"/><circle cx="36" cy="38" r="10"/><path d="M31 38h10"/></svg>
  <span>No DMV Hassles</span>
</div>

<div class="faq-photo" role="img" aria-label="Photo of a soldier in camouflage embracing a child holding a small flag"></div>
<h2 class="faq-title display">FREQUENTLY ASKED QUESTIONS</h2>
<div class="faq-item open" style="top:2462px"><span class="toggle">–</span>What types of vehicles can be donated?<svg class="chev" width="12" height="8" viewBox="0 0 12 8"><path d="M1 1l5 5 5-5" fill="none" stroke="#fff" stroke-width="2"/></svg></div>
<p class="faq-answer">We accept all vehicle donations, and in most cases, we also accept boats, motorcycles, RV's, and campers.</p>
<div class="faq-item" style="top:2583px"><span class="toggle">+</span>What paperwork do I need to donate my vehicle?<svg class="chev" width="8" height="12" viewBox="0 0 8 12"><path d="M1 1l5 5-5 5" fill="none" stroke="#333" stroke-width="2"/></svg></div>
<div class="faq-item" style="top:2628px"><span class="toggle">+</span>Is my donated vehicle tax-deductible?<svg class="chev" width="8" height="12" viewBox="0 0 8 12"><path d="M1 1l5 5-5 5" fill="none" stroke="#333" stroke-width="2"/></svg></div>
<div class="faq-item" style="top:2673px"><span class="toggle">+</span>What if the vehicle is not registered in my name?<svg class="chev" width="8" height="12" viewBox="0 0 8 12"><path d="M1 1l5 5-5 5" fill="none" stroke="#333" stroke-width="2"/></svg></div>
<div class="faq-item" style="top:2718px"><span class="toggle">+</span>When will I receive my tax receipt?<svg class="chev" width="8" height="12" viewBox="0 0 8 12"><path d="M1 1l5 5-5 5" fill="none" stroke="#333" stroke-width="2"/></svg></div>
<div class="faq-item" style="top:2763px"><span class="toggle">+</span>How do I schedule a pick up?<svg class="chev" width="8" height="12" viewBox="0 0 8 12"><path d="M1 1l5 5-5 5" fill="none" stroke="#333" stroke-width="2"/></svg></div>

<footer class="site-footer">
  <div class="foot-call">
    <svg width="30" height="48" viewBox="0 0 30 48"><rect x="2" y="2" width="26" height="44" rx="5" fill="none" stroke="#fff" stroke-width="3.5"/><line x1="2" y1="36" x2="28" y2="36" stroke="#fff" stroke-width="3"/></svg>
    <div class="foot-label display">CALL TODAY TO DONATE</div>
    <div class="foot-number display">1-800-555-0196</div>
    <div class="foot-hours">Live Operators Available-7 Days A Week</div>
  </div>
  <h4 class="foot-head display" style="left:514px">NAVIGATION</h4>
  <ul class="foot-nav">
    <li><svg width="13" height="10" viewBox="0 0 13 10"><path d="M1 5h9M7 1l4 4-4 4" fill="none" stroke="#fff" stroke-width="1.5"/></svg>HOW TO DONATE</li>
    <li><svg width="13" height="10" viewBox="0 0 13 10"><path d="M1 5h9M7 1l4 4-4 4" fill="none" stroke="#fff" stroke-width="1.5"/></svg>WHY DONATE</li>
    <li><svg width="13" height="10" viewBox="0 0 13 10"><path d="M1 5h9M7 1l4 4-4 4" fill="none" stroke="#fff" stroke-width="1.5"/></svg>FAQ</li>
    <li><svg width="13" height="10" viewBox="0 0 13 10"><path d="M1 5h9M7 1l4 4-4 4" fill="none" stroke="#fff" stroke-width="1.5"/></svg>ABOUT</li>
  </ul>
  <h4 class="foot-head display" style="left:724px">ABOUT RIDES FOR YOUTH</h4>
  <p class="foot-about">Nemo enim ipsam voluptatem quia voluptas sit aspe rnatur aut odit aut fugit, sed quia consequuntur magni dolores eos qui ratione voluptatem porro quisquam est, qui dolorem ipsum quias.</p>
  <div class="foot-rule"></div>
  <p class="copyright">Copyrights @ 2020 Rides For Youth. All Rights Reserved.</p>
</footer>

</body>
</html>
```